Company web site

Looking for a full responsive(mobile friendly) wordpress implementation

Some material is in the website -- brelvanto.wordpress.com

But looking for a template more consistent with the logo design, and more future looking.

Target Market(s)

Enterprise Clients

Industry/Entity Type

It Company

Font styles to use
Sans Serif

Colors
33a6d7
0255a3
0455a3
cfdeed
85abd2
3176b5

Requirements
Must have
• about, contact information, partner page, success stories, customer testimonials. links to social presence.
• pricing information

```html
<!DOCTYPE html>
<html lang="en">
<head>
<meta charset="utf-8">
<title>Brelvanto — Bridging Connected Devices With Enterprise Solutions</title>
<link rel="stylesheet" href="https://fonts.googleapis.com/css2?family=Lato:wght@400;700;900&family=Michroma&display=swap">
<style>
:root{
  --sky:#33a6d7;
  --navy:#0255a3;
  --royal:#3176b5;
  --mist:#cfdeed;
  --steel:#85abd2;
  --ink:#222;
  --text:#555;
  --grey-bg:#efefef;
  --dark:#4a4a4a;
}
*{box-sizing:border-box;margin:0;padding:0}
html,body{width:1200px;height:3488px;overflow:hidden}
body{font-family:"Lato",sans-serif;color:var(--text);background:#fff;position:relative}
section,header,footer{position:absolute;left:0;width:1200px}
.abs{position:absolute}
ul{list-style:none}

/* header */
.site-header{top:0;height:121px;background:#fff}
.brand{left:98px;top:30px;display:flex;align-items:center;gap:12px}
.brand-dot{width:40px;height:40px;border-radius:50%;background:var(--sky)}
.brand-name{font:700 30px "Lato",sans-serif;color:var(--navy)}
.contact-chip{top:24px;display:flex;gap:14px;align-items:flex-start}
.contact-chip .label{font:700 15px "Lato",sans-serif;color:#444;letter-spacing:.5px}
.contact-chip .value{font:700 16px "Lato",sans-serif;color:var(--sky)}
.main-nav{top:90px;left:0;width:1200px;height:24px}
.main-nav a{position:absolute;top:0;font:700 16px "Lato",sans-serif;color:#555;text-decoration:none}

/* hero */
.hero{top:121px;height:500px}
.hero-media{position:absolute;inset:0;background:linear-gradient(180deg,#5e6268 0%,#3d4a58 40%,#1f5f8e 70%,#202428 100%)}
.hero-caption{position:absolute;left:0;bottom:0;width:100%;height:63px;background:rgba(20,20,20,.82);display:flex;align-items:center;justify-content:center;font:400 30px "Michroma",sans-serif;color:#fff;letter-spacing:1px}

/* welcome */
.welcome{top:621px;height:383px;background:var(--grey-bg);text-align:center}
.welcome h1{position:absolute;top:48px;width:100%;font:400 38px "Michroma",sans-serif;color:#111}
.welcome h1 span{color:var(--sky)}
.welcome h1 .tail{color:#888}
.welcome .lead{position:absolute;top:128px;width:100%;font:700 17px "Lato",sans-serif;color:#222}
.welcome .body{position:absolute;top:170px;left:100px;width:1000px;font:400 15px/23px "Lato",sans-serif;color:#666;text-align:left}
.btn{position:absolute;display:flex;align-items:center;gap:12px;height:38px;padding:0 8px 0 18px;border-radius:19px;font:700 15px "Lato",sans-serif;color:#fff}
.btn i{width:26px;height:26px;border-radius:50%;background:#fff;display:flex;align-items:center;justify-content:center}
.btn-navy{background:var(--navy);left:535px;top:292px}

/* lifecycle */
.lifecycle{top:1004px;height:716px;background:#fff}
.lifecycle h2{position:absolute;top:50px;width:100%;text-align:center;font:700 33px "Lato",sans-serif;color:#111}
.lifecycle h2 span{font-weight:400;color:var(--sky)}
.lifecycle .sub{position:absolute;top:106px;width:100%;text-align:center;font:700 16px "Lato",sans-serif;color:#222}
.stage{position:absolute;background:#fff;box-shadow:0 1px 6px rgba(0,0,0,.18);padding:14px 16px 10px}
.stage h3{position:absolute;top:-26px;font:700 15px "Lato",sans-serif;color:var(--sky)}
.stage li{font:400 13px/19px "Lato",sans-serif;color:#333;padding-left:12px;position:relative}
.stage li::before{content:"";position:absolute;left:0;top:7px;width:5px;height:5px;border-radius:50%;background:var(--sky)}
.stage .num{position:absolute;font:700 56px "Lato",sans-serif;color:var(--mist);top:6px}
.stage .ico{position:absolute;width:48px;height:48px;border-radius:50%;background:var(--dark);border:3px solid #fff;box-shadow:0 0 0 1px #ccc;display:flex;align-items:center;justify-content:center}
.stage.right{text-align:right}
.stage.right li{padding-left:0;padding-right:12px}
.stage.right li::before{left:auto;right:0}

/* band */
.package-band{top:1720px;height:252px;background:linear-gradient(90deg,var(--royal),#2f80c2 50%,var(--royal))}
.package-band p{position:absolute;top:38px;width:100%;text-align:center;font:400 33px/50px "Michroma",sans-serif;color:#fff;letter-spacing:1px}
.btn-sky{background:var(--sky);left:526px;top:161px}

/* how it works */
.how{top:1972px;height:567px;background:#fff}
.section-title{position:absolute;width:100%;text-align:center;font:700 34px "Lato",sans-serif;color:#444}
.section-title span{font-weight:400;color:var(--sky)}
.section-rule{position:absolute;left:400px;width:400px;height:1px;background:#ddd}
.step-label{position:absolute;font:700 18px "Lato",sans-serif;color:#333}
.step-list li{font:400 14px/23px "Lato",sans-serif;color:#333;padding-left:12px;position:relative}
.step-list li::before{content:"";position:absolute;left:0;top:10px;width:5px;height:5px;border-radius:50%;background:#333}
.op{position:absolute;font:700 28px "Lato",sans-serif;color:#222}

/* testimonials */
.testimonials{top:2539px;height:325px;background:var(--grey-bg)}
.avatar{position:absolute;width:112px;height:112px;border-radius:50%;background:linear-gradient(135deg,#c9b8a6,#8e7d6e);border:5px solid var(--sky)}
.quote{position:absolute;width:370px;font:400 14px/21px "Lato",sans-serif;color:#333}
.quote b{color:var(--sky);font:900 30px/10px "Lato",sans-serif;vertical-align:-10px;margin-right:4px}
.quote-by{position:absolute;font:400 14px "Lato",sans-serif;color:#777}
.divider{position:absolute;left:599px;top:140px;width:1px;height:160px;background:#ccc}

/* partners */
.partners{top:2864px;height:275px;background:#fff}
.partner{position:absolute;top:135px;width:190px;height:88px;background:#fff;border:1px solid #ddd;display:flex;align-items:center;justify-content:center;font:700 20px "Lato",sans-serif;color:#222}

/* footer */
.site-footer{top:3139px;height:302px;background:var(--navy)}
.site-footer h4{position:absolute;top:42px;font:700 18px "Lato",sans-serif;color:#fff}
.site-footer h4 span{font-weight:400;color:var(--sky)}
.site-footer h4::after{content:"";position:absolute;left:0;top:30px;width:200px;height:1px;background:rgba(255,255,255,.3)}
.foot-links li{font:400 14px/32px "Lato",sans-serif;color:#fff;padding-left:12px;position:relative}
.foot-links li::before{content:"";position:absolute;left:0;top:14px;width:4px;height:4px;border-radius:50%;background:#fff}
.foot-text{font:400 14px/19px "Lato",sans-serif;color:#fff}
.foot-row{display:flex;align-items:center;gap:14px;font:400 14px "Lato",sans-serif;color:#fff}
.map{position:absolute;left:567px;top:88px;width:298px;height:121px;background:linear-gradient(135deg,#eceae4,#d8dde2);border:4px solid #fff}
.social{position:absolute;top:186px;width:28px;height:28px;border-radius:50%;background:var(--royal);border:2px solid #fff}
.copyright{top:3441px;height:47px;background:var(--sky);display:flex;align-items:center;justify-content:center;font:400 13px "Lato",sans-serif;color:#fff}
</style>
</head>
<body>

<header class="site-header">
  <div class="abs brand"><span class="brand-dot"></span><span class="brand-name">Brelvanto</span></div>
  <div class="abs contact-chip" style="left:632px">
    <svg width="34" height="34" viewBox="0 0 24 24"><path d="M6.6 10.8a15 15 0 0 0 6.6 6.6l2.2-2.2c.3-.3.7-.4 1-.2 1.1.4 2.3.6 3.6.6.6 0 1 .4 1 1V20c0 .6-.4 1-1 1A17 17 0 0 1 3 4c0-.6.4-1 1-1h3.5c.6 0 1 .4 1 1 0 1.3.2 2.5.6 3.6.1.3 0 .7-.2 1z" fill="var(--sky)"/></svg>
    <div><div class="label">CALL US</div><div class="value">+1-(555) 014-2750</div></div>
  </div>
  <div class="abs contact-chip" style="left:890px">
    <svg width="38" height="34" viewBox="0 0 24 22"><path d="M2 4h20v14H2z M2 4l10 8 10-8" fill="none" stroke="var(--sky)" stroke-width="2"/></svg>
    <div><div class="label">MAIL US</div><div class="value">info@brelvanto.com</div></div>
  </div>
  <nav class="abs main-nav">
    <svg class="abs" style="left:434px;top:-2px" width="24" height="22" viewBox="0 0 24 22"><path d="M12 2 1 12h3v9h6v-6h4v6h6v-9h3z" fill="var(--sky)"/></svg>
    <a style="left:492px">About</a>
    <a style="left:572px">Partner</a>
    <a style="left:666px">Success Stories</a>
    <a style="left:826px">Customer Testimonials</a>
    <a style="left:1036px">Contact</a>
  </nav>
</header>

<section class="hero">
  <div class="hero-media" role="img" aria-label="Hands holding a laptop and tablet with a glowing globe and a network of connected devices and people"></div>
  <div class="hero-caption">Bridging Connected Devices With Enterprise Solutions</div>
</section>

<section class="welcome">
  <h1>WelcomeTo <span>Brel</span><span class="tail">vanto</span></h1>
  <p class="lead">Founded in 2016 by industry veterans, Brelvanto is geared to provide integrated solutions for the IoT industry</p>
  <p class="body">Lorem ipsum dolor sit amet, consectetuer adipiscing elit, sed diam nonummy nibh euismod tincidunt ut laoreet dolore magna aliquam erat volutpat. Ut wisi enim ad minim veniam, quis nostrud exerci tation ullamcorper suscipit lobortis nisl ut aliquip ex ea commodo consequat. Duis autem vel eum iriure dolor in hendrerit in vulputate velit esse molestie consequat, vel illum dolore eu feugiat nulla facilisis at vero</p>
  <div class="btn btn-navy">Read More <i><svg width="12" height="12" viewBox="0 0 12 12"><path d="M4 2l4 4-4 4" fill="none" stroke="var(--navy)" stroke-width="2.4"/></svg></i></div>
</section>

<section class="lifecycle">
  <h2>Brelvanto Ensures End-to-end Product <span>Lifecycle Management</span></h2>
  <p class="sub">Closely engage with users throughout the entire process and increase customer lifetime value.</p>

  <svg class="abs" style="left:0;top:0" width="1200" height="716" viewBox="0 0 1200 716">
    <g fill="none" stroke="#999" stroke-width="1.5" stroke-dasharray="6 5">
      <path d="M600 279V286"/>
      <path d="M349 300H420L475 344"/>
      <path d="M849 310H790L725 344"/>
      <path d="M372 460H410L438 435"/>
      <path d="M832 470H790L762 435"/>
      <path d="M402 580H430L459 530"/>
      <path d="M802 580H770L741 530"/>
    </g>
    <circle cx="600" cy="449" r="163" fill="#e4e4e4"/>
    <circle cx="600" cy="449" r="92" fill="none" stroke="var(--sky)" stroke-width="18"/>
    <g fill="var(--sky)" stroke="#fff" stroke-width="3">
      <circle cx="600" cy="286" r="11"/>
      <circle cx="475" cy="344" r="11"/>
      <circle cx="725" cy="344" r="11"/>
      <circle cx="438" cy="435" r="11"/>
      <circle cx="762" cy="435" r="11"/>
      <circle cx="459" cy="530" r="11"/>
      <circle cx="741" cy="530" r="11"/>
    </g>
  </svg>

  <div class="stage" style="left:481px;top:200px;width:298px;height:79px">
    <h3 style="left:160px">Use</h3>
    <span class="num" style="left:10px">4</span>
    <ul style="margin-left:30px"><li>Customer web portal &amp; mobile apps</li><li>Notifications, social identity and advanced IoT services</li></ul>
    <span class="ico" style="right:-16px;top:-30px"><svg width="22" height="18"><rect x="2" y="2" width="18" height="14" rx="2" fill="none" stroke="#fff" stroke-width="2"/></svg></span>
  </div>

  <div class="stage" style="left:100px;top:244px;width:249px;height:107px">
    <h3 style="left:58px">Provision</h3>
    <span class="num" style="right:10px">3</span>
    <ul><li>Simplify consumer experience during device activation</li><li>P2P communication via Linkra</li></ul>
    <span class="ico" style="left:-4px;top:-46px"><svg width="20" height="20"><circle cx="10" cy="10" r="7" fill="none" stroke="#fff" stroke-width="2"/></svg></span>
  </div>

  <div class="stage right" style="left:849px;top:268px;width:260px;height:83px">
    <h3 style="right:66px">Support</h3>
    <span class="num" style="left:10px">5</span>
    <ul><li>In app chat, ticketing system and call center integration</li></ul>
    <span class="ico" style="right:4px;top:-46px"><svg width="20" height="20"><circle cx="10" cy="8" r="5" fill="#fff"/><rect x="3" y="14" width="14" height="5" rx="2" fill="#fff"/></svg></span>
  </div>

  <div class="stage" style="left:116px;top:403px;width:256px;height:116px">
    <h3 style="left:58px">Sell</h3>
    <span class="num" style="right:10px">2</span>
    <ul><li>End user tracking in CRM</li><li>Social identity for proactive marketing</li></ul>
    <span class="ico" style="left:-4px;top:-46px"><svg width="20" height="20"><rect x="4" y="4" width="12" height="12" fill="none" stroke="#fff" stroke-width="2"/></svg></span>
  </div>

  <div class="stage right" style="left:832px;top:426px;width:242px;height:97px">
    <h3 style="right:66px">Monetize</h3>
    <span class="num" style="left:10px">6</span>
    <ul><li>Recurrent user billing</li><li>Additional services &amp; payment options.</li></ul>
    <span class="ico" style="right:-16px;top:-46px"><svg width="20" height="20"><circle cx="10" cy="10" r="7" fill="#fff"/></svg></span>
  </div>

  <div class="stage" style="left:153px;top:554px;width:249px;height:111px">
    <h3 style="left:58px">Manufacture</h3>
    <span class="num" style="right:10px">1</span>
    <ul><li>Secure manufacturing process</li><li>Device traceability in ERP</li></ul>
    <span class="ico" style="left:-4px;top:-46px"><svg width="20" height="20"><circle cx="10" cy="10" r="6" fill="none" stroke="#fff" stroke-width="3" stroke-dasharray="3 2"/></svg></span>
  </div>

  <div class="stage right" style="left:802px;top:554px;width:263px;height:111px">
    <h3 style="right:66px">Maintain</h3>
    <span class="num" style="left:10px">7</span>
    <ul><li>Device health check</li><li>Software and security updates</li></ul>
    <span class="ico" style="right:4px;top:-46px"><svg width="20" height="20"><rect x="4" y="3" width="12" height="15" rx="2" fill="none" stroke="#fff" stroke-width="2"/></svg></span>
  </div>
</section>

<section class="package-band">
  <p>A complete package that links IoT clouds<br>with enterprise software solutions</p>
  <div class="btn btn-sky">Get Started <i><svg width="12" height="12" viewBox="0 0 12 12"><path d="M4 2l4 4-4 4" fill="none" stroke="var(--sky)" stroke-width="2.4"/></svg></i></div>
</section>

<section class="how">
  <h2 class="section-title" style="top:42px">How It <span>Works</span></h2>
  <div class="section-rule" style="top:100px"></div>

  <svg class="abs" style="left:0;top:0" width="1200" height="567" viewBox="0 0 1200 567">
    <g fill="none" stroke="var(--sky)" stroke-width="5">
      <path d="M105 423H100M163 360L465 255L739 423L1046 255"/>
      <path d="M100 423C100 380 130 360 163 360"/>
    </g>
    <g fill="#fff" stroke="var(--sky)" stroke-width="5">
      <circle cx="163" cy="423" r="63"/>
      <circle cx="465" cy="255" r="63"/>
      <circle cx="739" cy="423" r="63"/>
      <circle cx="1046" cy="255" r="63"/>
    </g>
    <g fill="var(--sky)">
      <circle cx="200" cy="372" r="8"/><circle cx="515" cy="300" r="8"/>
      <circle cx="690" cy="383" r="8"/><circle cx="1000" cy="216" r="8"/>
    </g>
    <g fill="#2a2a2a">
      <path d="M135 418l28 8 28-8v26l-28 8-28-8z"/>
      <circle cx="163" cy="398" r="10"/>
      <g fill="none" stroke="#2a2a2a" stroke-width="8" stroke-linecap="round">
        <rect x="438" y="255" width="30" height="16" rx="8" transform="rotate(-45 453 263)"/>
        <rect x="462" y="239" width="30" height="16" rx="8" transform="rotate(-45 477 247)"/>
      </g>
      <circle cx="739" cy="423" r="20" fill="none" stroke="#2a2a2a" stroke-width="10" stroke-dasharray="6 4"/>
      <circle cx="739" cy="423" r="7"/>
      <g stroke="#2a2a2a" stroke-width="3">
        <path d="M1046 255L1020 232M1046 255L1074 234M1046 255L1024 280M1046 255L1070 282"/>
      </g>
      <circle cx="1046" cy="255" r="9"/><circle cx="1020" cy="232" r="6"/><circle cx="1074" cy="234" r="6"/><circle cx="1024" cy="280" r="6"/><circle cx="1070" cy="282" r="6"/>
    </g>
  </svg>

  <span class="step-label" style="left:135px;top:271px">Learn</span>
  <span class="step-label" style="left:420px;top:159px">Connect</span>
  <span class="step-label" style="left:694px;top:271px">Integrate</span>
  <span class="step-label" style="left:936px;top:159px">Connected Product</span>
  <span class="op" style="left:302px;top:318px">×</span>
  <span class="op" style="left:578px;top:292px">×</span>
  <span class="op" style="left:860px;top:276px">=</span>

  <ul class="abs step-list" style="left:124px;top:498px"><li>Properties</li><li>Actions</li><li>Events</li></ul>
  <ul class="abs step-list" style="left:428px;top:330px"><li>Stratus IoT</li><li>Cobalt IoT</li><li>Linkra</li><li>Arvenu</li><li>Thingwell</li><li style="padding-left:0">... and others</li></ul>
  <ul class="abs step-list" style="left:628px;top:498px"><li>CRM systems</li><li>Social login</li><li>Billing</li></ul>
  <ul class="abs step-list" style="left:774px;top:498px"><li>HelpLoom</li><li>Triggr</li><li style="padding-left:0">... and many others</li></ul>
</section>

<section class="testimonials">
  <h2 class="section-title" style="top:42px">Client <span>Testimonials</span></h2>
  <div class="section-rule" style="top:100px;background:#d5d5d5"></div>
  <svg class="abs" style="left:58px;top:178px" width="22" height="40"><path d="M18 2L4 20l14 18" fill="none" stroke="#c8c8c8" stroke-width="3"/></svg>
  <svg class="abs" style="left:1120px;top:178px" width="22" height="40"><path d="M4 2l14 18L4 38" fill="none" stroke="#c8c8c8" stroke-width="3"/></svg>

  <div class="avatar" style="left:97px;top:137px" role="img" aria-label="Portrait of a smiling male client"></div>
  <p class="quote" style="left:221px;top:140px"><b>“</b>Duis autem vel eumk iriure dolor at veromoli eros dignissim qui blandit praesent luptatum hok quis nostrud exerci tation ullamcorper susc zzrilm deleni augue duis facilisi.</p>
  <span class="quote-by" style="left:221px;top:252px">- Mr. Tomas Ferrand</span>

  <div class="divider"></div>

  <div class="avatar" style="left:653px;top:137px" role="img" aria-label="Portrait of a smiling female client"></div>
  <p class="quote" style="left:777px;top:140px"><b>“</b>Duis autem vel eumk iriure dolor at veromoli eros dignissim qui blandit praesent luptatum hok quis nostrud exerci tation ullamcorper susc zzrilm deleni augue duis facilisi.</p>
  <span class="quote-by" style="left:777px;top:252px">- Mrs. Aline Corwy</span>
</section>

<section class="partners">
  <h2 class="section-title" style="top:42px">Our <span>Partners</span></h2>
  <div class="section-rule" style="top:100px"></div>
  <svg class="abs" style="left:46px;top:160px" width="22" height="40"><path d="M18 2L4 20l14 18" fill="none" stroke="#ccc" stroke-width="3"/></svg>
  <svg class="abs" style="left:1130px;top:160px" width="22" height="40"><path d="M4 2l14 18L4 38" fill="none" stroke="#ccc" stroke-width="3"/></svg>
  <div class="partner" style="left:98px">Ledgerly</div>
  <div class="partner" style="left:302px">Brightpane</div>
  <div class="partner" style="left:507px">Velmora</div>
  <div class="partner" style="left:707px">Oakhaven</div>
  <div class="partner" style="left:911px">Quadrex</div>
</section>

<footer class="site-footer">
  <h4 style="left:100px">Quick <span>Links</span></h4>
  <ul class="abs foot-links" style="left:100px;top:84px">
    <li>Home</li><li>About</li><li>Partner</li><li>Success Stories</li><li>Customer Testimonials</li><li>Contact</li>
  </ul>

  <h4 style="left:328px">Contact <span>Details</span></h4>
  <div class="abs foot-text" style="left:328px;top:88px">Brelvanto<br>418 Harbor Way<br>Lindale, CA 90210</div>
  <div class="abs foot-row" style="left:328px;top:172px"><svg width="16" height="16" viewBox="0 0 24 24"><path d="M6.6 10.8a15 15 0 0 0 6.6 6.6l2.2-2.2c.3-.3.7-.4 1-.2 1.1.4 2.3.6 3.6.6.6 0 1 .4 1 1V20c0 .6-.4 1-1 1A17 17 0 0 1 3 4c0-.6.4-1 1-1h3.5c.6 0 1 .4 1 1 0 1.3.2 2.5.6 3.6.1.3 0 .7-.2 1z" fill="#fff"/></svg>+1-(555) 014-2750</div>
  <div class="abs foot-row" style="left:328px;top:212px"><svg width="16" height="16" viewBox="0 0 24 24"><rect x="3" y="4" width="18" height="16" rx="2" fill="#fff"/></svg>+1-(555) 014-2750</div>
  <div class="abs foot-row" style="left:328px;top:252px"><svg width="16" height="14" viewBox="0 0 24 20"><path d="M2 2h20v16H2z M2 2l10 8 10-8" fill="none" stroke="#fff" stroke-width="2"/></svg>info@brelvanto.com</div>

  <h4 style="left:567px">Location <span>Map</span></h4>
  <div class="map" role="img" aria-label="Street map showing the office location at 418 Harbor Way"></div>

  <div class="abs" style="left:949px;top:92px;display:flex;align-items:center;gap:10px">
    <span style="width:34px;height:34px;border-radius:50%;background:#fff"></span>
    <span style="font:700 26px 'Lato',sans-serif;color:#fff">Brelvanto</span>
  </div>
  <span class="social" style="left:955px"></span>
  <span class="social" style="left:991px"></span>
  <span class="social" style="left:1027px"></span>
  <span class="social" style="left:1063px"></span>
</footer>
<div class="abs copyright" style="left:0;width:1200px">Copyright © 2017 Brelvanto. All Rights Reserved.</div>

</body>
</html>
```